Jolly Hounds Dog Behaviour, Training and Natural Healthcare Business Card Design

I am an experienced and qualified dog behavioural trainer and natural animal healthcare consultant offering a range of services to help pet dog owners with the "whole dog".
COLOURS: A soft light blue in the background - can be fading out or split, red should also feature
LOGO: Dog, healing hands, silhouette, shadow
SERVICES: Behaviour Consults, Training, Complex Skills Coaching Walking Coaching, Diet & Nutrition, Environmental Enrichment, Lifestyle and Lifestage Adaptations, Massage, Natural Health Options
BY LINE: Happy Dogs, Happy Owners
VALUES: Promoting communication and connection between dogs and their owners.
FOCUS: Nutritional guidance and environmental adaptation are often needed to complete the package and increase the success rate of training and behaviour modification.

Target Market(s)

Everyone who has a dog who they wish to improve their relationship with

Industry/Entity Type

Communication

Contact Information for Business Card

Jolly Hounds, Rebecca Thornbury, 0427 861350, jollyhounds7@fernpost.example, www.jollyhounds7.example, Qualified Dog Behavioural Trainer and Natural Animal Healthcare Consultant

Font styles to use
Sans Serif
Script

Colors
85cae6
ec2027

Requirements
Must have
• A clear indication that it is a dog services business. A raised feature
Should not have
• Pawprints, cartoons

```html
<!DOCTYPE html>
<html lang="en">
<head>
<meta charset="utf-8">
<title>Jolly Hounds Business Card</title>
<link rel="stylesheet" href="https://fonts.googleapis.com/css2?family=Open+Sans:ital,wght@0,400;0,600;0,700;1,600&family=Dancing+Script:wght@600&display=swap">
<style>
  :root {
    --sky-blue: #85cae6;
    --sky-blue-soft: #d6eef8;
    --band-dark: #3b3c3c;
    --swoosh-white: #ffffff;
    --brand-red: #ec2027;
    --text-light: #ffffff;
    --photo-gold: #d9b27a;
    --photo-shade: #2f3a24;
  }
  html, body {
    margin: 0;
    padding: 0;
    width: 1200px;
    height: 900px;
    overflow: hidden;
    background: linear-gradient(180deg, var(--sky-blue) 0%, var(--sky-blue-soft) 100%);
  }
  .business-card {
    position: absolute;
    left: 75px;
    top: 150px;
    width: 1050px;
    height: 600px;
    overflow: hidden;
    box-shadow: 0 12px 32px rgba(20, 60, 80, 0.3);
    font-family: "Open Sans", sans-serif;
    color: var(--text-light);
  }
  .card-shapes {
    position: absolute;
    inset: 0;
    display: block;
  }
  .brand-name {
    position: absolute;
    left: 440px;
    top: 14px;
    margin: 0;
    font-size: 60px;
    font-weight: 700;
    line-height: 1;
    letter-spacing: 0.5px;
  }
  .brand-tagline {
    position: absolute;
    left: 380px;
    top: 86px;
    width: 520px;
    margin: 0;
    font-size: 18px;
    font-weight: 600;
    line-height: 24px;
    text-align: center;
  }
  .holder-name {
    position: absolute;
    left: 560px;
    top: 350px;
    margin: 0;
    font-family: "Dancing Script", cursive;
    font-size: 54px;
    font-weight: 600;
    line-height: 1;
  }
  .holder-phone {
    position: absolute;
    left: 564px;
    top: 424px;
    margin: 0;
    font-size: 28px;
    font-weight: 600;
    letter-spacing: 1px;
  }
  .contact-line {
    position: absolute;
    top: 522px;
    display: flex;
    align-items: center;
    gap: 10px;
    font-size: 22px;
    font-style: italic;
    font-weight: 600;
  }
  .contact-email { left: 50px; }
  .contact-web { left: 580px; }
  .contact-icon { width: 20px; height: 20px; flex: none; }
</style>
</head>
<body>
  <section class="business-card">
    <svg class="card-shapes" viewBox="0 0 1050 600" width="1050" height="600">
      <defs>
        <linearGradient id="puppy-photo-tone" x1="0" y1="0" x2="1" y2="0.4">
          <stop offset="0" stop-color="#3d4a2c"/>
          <stop offset="0.3" stop-color="#d9b27a"/>
          <stop offset="0.7" stop-color="#c89a5e"/>
          <stop offset="1" stop-color="#1f2619"/>
        </linearGradient>
      </defs>
      <rect class="dark-band" x="0" y="0" width="1050" height="600" fill="var(--band-dark)"/>
      <path class="puppy-photo" d="M0 135 L700 135 L700 320 C 470 345 230 350 0 350 Z" fill="url(#puppy-photo-tone)" role="img" aria-label="Photo of two golden retriever puppies"/>
      <path class="white-swoosh" d="M0 340 C 420 345 760 260 1050 115 L1050 600 L0 600 Z" fill="var(--swoosh-white)"/>
      <path class="red-panel" d="M0 360 C 450 360 800 300 1050 230 L1050 600 L0 600 Z" fill="var(--brand-red)"/>
    </svg>

    <h1 class="brand-name">Jolly Hounds</h1>
    <p class="brand-tagline">Qualified Dog Behavioural<br>Trainer and Natural Animal Healthcare Consultant</p>

    <p class="holder-name">Rebecca Thornbury</p>
    <p class="holder-phone">0427 861350</p>

    <div class="contact-line contact-email">
      <svg class="contact-icon" viewBox="0 0 20 20" aria-hidden="true">
        <circle cx="10" cy="10" r="10" fill="#ffffff"/>
        <rect x="4.5" y="6.5" width="11" height="7.5" fill="none" stroke="var(--brand-red)" stroke-width="1.4"/>
        <path d="M4.5 6.5 L10 11 L15.5 6.5" fill="none" stroke="var(--brand-red)" stroke-width="1.4"/>
      </svg>
      <span>jollyhounds7@fernpost.example</span>
    </div>
    <div class="contact-line contact-web">
      <svg class="contact-icon" viewBox="0 0 20 20" aria-hidden="true">
        <circle cx="10" cy="10" r="10" fill="#ffffff"/>
        <circle cx="10" cy="10" r="6" fill="none" stroke="var(--brand-red)" stroke-width="1.3"/>
        <ellipse cx="10" cy="10" rx="2.6" ry="6" fill="none" stroke="var(--brand-red)" stroke-width="1.1"/>
        <path d="M4 10 H16" stroke="var(--brand-red)" stroke-width="1.1"/>
      </svg>
      <span>www.jollyhounds7.example</span>
    </div>
  </section>
</body>
</html>
```